verdant terraces simple classy business card design

my name is colin barrow and I run a gardening business aimed at high class verdant terraces. the business name is verdant terraces and our logo was designed on pixel harbour .My clientel are anything from residential homes to businesses. I take pride in my work and know that I offer a service like no other in my area.
The business card will be used to represent my business and I want it to be not only rememberable, but simplistic and modern. Eye catching too. Of course I would like it relatable to gardening and appealing to the correct clientel - those being garden enthusiasts, prestigious homes and businesses that are after top of the line gardening services like no other on the market.
I am not a typical lawn mowing business so I don't want a typical card design that represents that. The gardens I work with are generally million dollar properties with owners who are very garden proud looking for upkeep and guidance from me along with sometimes whole new garden designs. I want the business cards to show to my clients that I take pride, as they do, in their garden. And I want them to know from my card that I am a professional, qualified horticulturist offering them a top of the line service for life. I want them to refer my business on. I want them to look at my business card and see class and professionalism in a modern unique bold way.
The card should be simple with the possibility of the logo on the front being embossed/debossed and my details on the back the card should have a organic garden feel it's very important to me that it is absolutely perfect
I am also very open to ideas and suggestions so look forward to seeing the designs. the business logo has been supplied with this project and I want the card to be double sided

Contact info is
Colin Barrow - Managing Director / Horticulturist
Phone : 0481 526 704
Email: colinbarrow@verdantterraces.example.au

Target Market(s)

high class gardens residential and commercial

Industry/Entity Type

Gardener

Contact Information for Business Card

Contact info is
Phone : 0481 526 704

PLEASE MAKE CARD DOUBLE SIDED

Requirements
Must have
• organic simple classy modern feel
• must flow with the current logo that has been supplied with this project
• Double sided
• Must explain in a simple way that I deal with high end gardens and I'm a qualified horticulturist
Nice to have
• embossed debossed logo
Should not have
• shouldn't be to busy or cheap looking

```html
<!DOCTYPE html>
<html lang="en">
<head>
<meta charset="utf-8">
<title>Verdant Terraces – Business Card</title>
<link rel="stylesheet" href="https://fonts.googleapis.com/css2?family=Arimo:wght@400;600&family=Cinzel:wght@400&display=swap">
<style>
  :root {
    --backdrop: #9a9a9a;
    --card-white: #eeefee;
    --leaf-green: #4f8a45;
    --band-grey: #7b7c7d;
    --ink: #2b2b2b;
    --mark-light: #e9ede6;
  }
  * { margin: 0; padding: 0; box-sizing: border-box; }
  html, body {
    width: 1105px;
    height: 1200px;
    overflow: hidden;
    background: var(--backdrop);
  }
  .card {
    position: absolute;
    left: 182px;
    width: 747px;
    height: 427px;
    overflow: hidden;
  }
  .card--front { top: 119px; background: var(--card-white); }
  .card--back { top: 635px; background: var(--leaf-green); }

  .brand {
    position: absolute;
    display: flex;
    flex-direction: column;
    align-items: center;
    font-family: "Cinzel", Georgia, serif;
    font-weight: 400;
    line-height: 1;
  }
  .brand__dot {
    border-radius: 50%;
    margin-bottom: 10px;
  }
  .brand__primary { letter-spacing: 0.02em; }
  .brand__secondary { margin-top: 6px; }

  .card--front .brand {
    left: 402px;
    width: 304px;
    top: 28px;
    color: var(--leaf-green);
  }
  .card--front .brand__dot {
    width: 84px; height: 84px;
    background: var(--leaf-green);
  }
  .card--front .brand__primary { font-size: 34px; }
  .card--front .brand__secondary { font-size: 22px; letter-spacing: 0.55em; margin-right: -0.55em; }

  .card--back .brand {
    left: 0;
    width: 100%;
    top: 118px;
    color: var(--mark-light);
  }
  .card--back .brand__dot {
    width: 108px; height: 108px;
    background: var(--mark-light);
  }
  .card--back .brand__primary { font-size: 40px; }
  .card--back .brand__secondary { font-size: 26px; letter-spacing: 0.6em; margin-right: -0.6em; }

  .contact {
    position: absolute;
    left: 28px;
    top: 229px;
    font-family: "Arimo", Arial, sans-serif;
    color: var(--ink);
  }
  .contact__name {
    font-size: 25px;
    font-weight: 600;
    color: var(--leaf-green);
    line-height: 1.1;
  }
  .contact__role {
    font-size: 19px;
    margin-top: 10px;
  }
  .contact__line {
    font-size: 18px;
    margin-top: 14px;
  }
  .contact__line + .contact__line { margin-top: 10px; }
  .contact__label {
    color: var(--leaf-green);
    font-weight: 600;
  }

  .footer-band {
    position: absolute;
    left: 0;
    bottom: 0;
    width: 747px;
    height: 50px;
  }
  .website {
    position: absolute;
    left: 22px;
    bottom: 12px;
    font-family: "Arimo", Arial, sans-serif;
    font-size: 18px;
    letter-spacing: 0.14em;
    color: #ffffff;
  }
</style>
</head>
<body>
  <section class="card card--front" aria-label="Business card front">
    <div class="brand">
      <span class="brand__dot"></span>
      <span class="brand__primary">VERDANT</span>
      <span class="brand__secondary">TERRACES</span>
    </div>

    <div class="contact">
      <p class="contact__name">Colin Barrow</p>
      <p class="contact__role">Managing Director / Horticulturist</p>
      <p class="contact__line"><span class="contact__label">P</span> : 0481 526 704</p>
      <p class="contact__line"><span class="contact__label">E</span> : colinbarrow@verdantterraces.example.au</p>
    </div>

    <svg class="footer-band" viewBox="0 0 747 50" aria-hidden="true">
      <polygon points="0,0 372,0 396,50 0,50" fill="var(--leaf-green)"/>
      <polygon points="392,12 747,12 747,31 404,31" fill="var(--band-grey)"/>
    </svg>
    <p class="website">verdantterraces.example.au</p>
  </section>

  <section class="card card--back" aria-label="Business card back">
    <div class="brand">
      <span class="brand__dot"></span>
      <span class="brand__primary">VERDANT</span>
      <span class="brand__secondary">TERRACES</span>
    </div>
  </section>
</body>
</html>
```